A Spin Above Par Company Brochure

I am the owner of a Mobile Disc Jockey company specializing in weddings. I am looking for a Tri Fold color brochure that is modern and eye catching with the focus being on upscale wedding events. I also want it to be easy to read and not overly cluttered ! I would like it to reflect our website located at aspinabovepar.example
I also have different variations and file types of my logo such as jpeg and png files. I need some good dance floor pics. If you do not have any good stock photos I can look through my photo library. I uploaded a logo and pic I found from one of my videos. Not sure if it is worth anything.
We also do Uplighting and Photo Booths which I would like in the brochure. Much of the text copy needed can be taken from our website if needed. Please refer to the website to see what we do and our style.

Target Market(s)

upscale weddings

Industry/Entity Type

wedding dj entertainment & masters of ceremonies

Requirements
Nice to have
• nice pictures of packed dance floors and people having fun

```html
<!DOCTYPE html>
<html lang="en">
<head>
<meta charset="utf-8">
<title>A Spin Above Par – Tri Fold Brochure</title>
<link href="https://fonts.googleapis.com/css2?family=Montserrat:wght@400;500;600;700;800&display=swap" rel="stylesheet">
<style>
:root{
  --purple:#7d3196;
  --purple-deep:#3b1a86;
  --purple-mid:#5a2aa0;
  --pink:#e8195a;
  --white:#ffffff;
  --ink:#1e1e24;
  --grey:#6e6e74;
  --stage:#dcdcdf;
}
*{margin:0;padding:0;box-sizing:border-box}
html,body{width:1200px;height:962px;overflow:hidden}
body{background:var(--stage);font-family:'Montserrat',sans-serif;color:var(--ink);position:relative}
.spread-frame{position:absolute;left:275px;width:650px;height:460px;overflow:hidden}
.spread-frame.outside{top:14px}
.spread-frame.inside{top:488px}
.spread{position:relative;width:1062px;height:751px;transform:scale(.612);transform-origin:0 0;background:var(--white);overflow:hidden}
.spread > svg.shapes{position:absolute;inset:0;width:1062px;height:751px}
.abs{position:absolute}
.section-title{color:var(--pink);font-weight:800;font-size:22px;letter-spacing:.2px;text-transform:uppercase}
.body-copy{font-size:13.2px;line-height:16.4px;text-align:justify;font-weight:500}
.body-copy p+p{margin-top:13px}
.brand-name{font-weight:600;white-space:nowrap}
.contact-list{list-style:none}
.contact-list li{display:flex;align-items:center;gap:22px;color:var(--white);font-size:16px;height:28px}
.contact-list svg{width:18px;height:18px}
.tagline{color:var(--white);text-align:center}
.tagline h2{font-weight:800;font-size:26px;line-height:30px}
.tagline .rule{width:150px;height:2px;background:var(--pink);margin:4px auto 8px}
.tagline p{font-weight:600;font-size:16px;line-height:19px}
.checklist{list-style:none}
.checklist li{display:flex;align-items:center;gap:14px;color:var(--purple);font-size:19px;font-weight:500;height:41.5px}
.checklist svg{width:20px;height:20px;flex:none}
.quote{color:var(--white);font-size:9.6px;line-height:11.3px;text-align:justify;font-weight:500}
.quote-author{color:var(--pink);font-size:15px;font-weight:500}
.services{list-style:none;font-size:11.4px;line-height:16.3px;font-weight:500}
.services li{position:relative;padding-left:17px;margin-bottom:5px}
.services li::before{content:"";position:absolute;left:0;top:5px;width:6px;height:6px;border-radius:50%;background:var(--pink)}
.white-text{color:var(--white)}
</style>
</head>
<body>

<!-- OUTSIDE SPREAD -->
<div class="spread-frame outside">
<section class="spread">
  <svg class="shapes" viewBox="0 0 1062 751" aria-hidden="false">
    <defs>
      <linearGradient id="photoDeck" x1="0" y1="0" x2="1" y2="1">
        <stop offset="0" stop-color="#1d1450"/>
        <stop offset=".45" stop-color="#3b2296"/>
        <stop offset=".75" stop-color="#7a2a8c"/>
        <stop offset="1" stop-color="#d2306a"/>
      </linearGradient>
      <radialGradient id="floorPhoto" cx=".5" cy=".5" r=".5">
        <stop offset="0" stop-color="#a48a7a"/>
        <stop offset=".7" stop-color="#5a4540"/>
        <stop offset="1" stop-color="#2e2420"/>
      </radialGradient>
    </defs>
    <!-- photo area across back and cover panels -->
    <rect x="353" y="0" width="709" height="620" fill="url(#photoDeck)" role="img" aria-label="Photo: a DJ's hand over a glowing mixing deck"/>
    <!-- panel 1 bottom waves -->
    <path d="M0 600 Q180 610 353 520 V751 H0 Z" fill="var(--pink)"/>
    <path d="M0 650 Q180 660 353 540 V751 H0 Z" fill="var(--purple)"/>
    <!-- panel 2 bottom -->
    <path d="M353 545 Q380 520 420 520 Q520 515 690 515 L690 751 H353 Z" fill="var(--purple)"/>
    <!-- panel 3 bottom -->
    <path d="M690 515 Q760 580 880 560 Q1000 535 1062 440 V751 H690 Z" fill="var(--purple)"/>
    <!-- cover top right corner -->
    <path d="M800 0 Q850 95 960 118 Q1010 125 1062 118 V0 Z" fill="var(--pink)"/>
    <path d="M812 0 Q860 82 960 100 Q1010 107 1062 100 V0 Z" fill="var(--white)"/>
    <!-- panel folds -->
    <line x1="353" y1="0" x2="353" y2="751" stroke="#000" stroke-opacity=".12"/>
    <line x1="690" y1="0" x2="690" y2="751" stroke="#000" stroke-opacity=".12"/>
    <!-- circle photo -->
    <circle cx="210" cy="608" r="103" fill="none" stroke="var(--pink)" stroke-width="2"/>
    <circle cx="210" cy="608" r="98" fill="url(#floorPhoto)" role="img" aria-label="Photo: guests dancing at a wedding reception"/>
  </svg>

  <h3 class="abs section-title" style="left:35px;top:122px">About Us</h3>
  <div class="abs body-copy" style="left:35px;top:165px;width:288px">
    <p>A Spin Above Par is a professional wedding DJ, lighting and photobooth company operating out of Estero, Florida and serving the Naples, Fort Myers, Captiva, Marco &amp; Sanibel Islands and surrounding areas. We bring a wealth of expertise, fun and knowledge to every celebration and constantly exceed our client's expectations. Our talented team of DJs and MCs are passionate about making your event an unforgettable party.</p>
    <p>We know how much work goes into planning a wedding or the simplest event so we've created a simple process to make planning your wedding or event easy, fun and stress free! For weddings everything from your ceremony to the end of your reception will be crafted your way for an experience your guests will be talking about for years to come.</p>
  </div>

  <div class="abs brand-name white-text" style="left:405px;top:552px;font-size:26px">A Spin Above Par</div>
  <h3 class="abs section-title" style="left:405px;top:612px">Contact Us</h3>
  <ul class="abs contact-list" style="left:405px;top:642px">
    <li><svg viewBox="0 0 24 24"><path fill="var(--pink)" d="M6.6 10.8a15 15 0 006.6 6.6l2.2-2.2c.3-.3.7-.4 1-.2 1.1.4 2.3.6 3.6.6.6 0 1 .4 1 1V20c0 .6-.4 1-1 1C10.6 21 3 13.4 3 4c0-.6.4-1 1-1h3.5c.6 0 1 .4 1 1 0 1.3.2 2.5.6 3.6.1.3 0 .7-.2 1z"/></svg>555.014.2290</li>
    <li><svg viewBox="0 0 24 24"><rect x="2" y="5" width="20" height="14" rx="2" fill="var(--pink)"/><path d="M3 6l9 7 9-7" fill="none" stroke="var(--purple)" stroke-width="1.6"/></svg>hello@aspinabovepar.example</li>
    <li><svg viewBox="0 0 24 24"><circle cx="12" cy="12" r="10" fill="var(--pink)"/><path d="M2 12h20M12 2c3 3 3 17 0 20M12 2c-3 3-3 17 0 20" fill="none" stroke="var(--purple)" stroke-width="1.3"/></svg>www.aspinabovepar.example</li>
  </ul>

  <div class="abs brand-name" style="left:880px;top:40px;font-size:20px;color:var(--grey)">A Spin Above Par</div>

  <div class="abs tagline" style="left:700px;top:595px;width:352px">
    <h2>MODERN, TASTEFUL, &amp;<br>FUN ENTERTAINMENT</h2>
    <div class="rule"></div>
    <p>Weddings, Corporate Events,<br>Private Parties, any event is better<br>with A Spin Above Par</p>
  </div>
</section>
</div>

<!-- INSIDE SPREAD -->
<div class="spread-frame inside">
<section class="spread">
  <svg class="shapes" viewBox="0 0 1062 751">
    <defs>
      <linearGradient id="partyPhoto" x1="0" y1="0" x2="1" y2="1">
        <stop offset="0" stop-color="#e7d8c6"/>
        <stop offset=".4" stop-color="#b04a3c"/>
        <stop offset="1" stop-color="#6b5a7e"/>
      </linearGradient>
      <radialGradient id="hallPhoto" cx=".5" cy=".5" r=".5">
        <stop offset="0" stop-color="#b57be0"/>
        <stop offset="1" stop-color="#3a1a6e"/>
      </radialGradient>
      <radialGradient id="dancePhoto" cx=".5" cy=".5" r=".5">
        <stop offset="0" stop-color="#e8d6c4"/>
        <stop offset="1" stop-color="#8a6a58"/>
      </radialGradient>
      <radialGradient id="avatar" cx=".5" cy=".5" r=".5">
        <stop offset="0" stop-color="#f1dcc0"/>
        <stop offset="1" stop-color="#c49a6a"/>
      </radialGradient>
    </defs>
    <!-- purple top across panels 1 and 2 -->
    <path d="M0 0 H713 V248 Q560 245 420 252 Q240 262 150 300 Q60 340 0 430 Z" fill="var(--purple)"/>
    <path d="M0 430 Q60 340 150 300 Q240 262 420 252 Q560 245 713 248 V262 Q560 258 420 265 Q250 275 160 315 Q70 355 0 462 Z" fill="var(--pink)"/>
    <!-- panel 3 photo -->
    <path d="M713 0 H1064 V345 Q960 430 820 418 Q750 410 713 380 Z" fill="url(#partyPhoto)" role="img" aria-label="Photo: wedding guests cheering with arms raised on a packed dance floor"/>
    <path d="M820 418 Q960 430 1064 345 V368 Q960 448 820 432 Z" fill="var(--pink)"/>
    <!-- folds -->
    <line x1="344" y1="0" x2="344" y2="751" stroke="#000" stroke-opacity=".12"/>
    <line x1="713" y1="0" x2="713" y2="751" stroke="#000" stroke-opacity=".12"/>
    <!-- circles -->
    <circle cx="122" cy="351" r="98" fill="none" stroke="var(--pink)" stroke-width="2"/>
    <circle cx="122" cy="351" r="93" fill="url(#hallPhoto)" role="img" aria-label="Photo: reception hall with purple uplighting"/>
    <circle cx="742" cy="348" r="60" fill="url(#dancePhoto)" role="img" aria-label="Photo: couple's first dance surrounded by guests"/>
    <circle cx="440" cy="110" r="31" fill="url(#avatar)" role="img" aria-label="Photo: smiling bride"/>
    <!-- quote marks -->
    <path d="M607 218 q0 -14 12 -20 l2 4 q-6 4 -6 9 a8 8 0 1 1 -8 7z M627 218 q0 -14 12 -20 l2 4 q-6 4 -6 9 a8 8 0 1 1 -8 7z" fill="var(--pink)"/>
  </svg>

  <h3 class="abs section-title" style="left:34px;top:34px">DJ Entertainment</h3>
  <div class="abs body-copy white-text" style="left:34px;top:72px;width:288px">
    <p>Let our team of professional DJs and Emcees keep your guests entertained and on the dance floor all night long! We have helped countless couples plan their destination wedding as if they were here just like our local clients. Whether you're planning an intimate reception for a small group of 20 of your closest family and friends or a larger more elaborate event with a guest list of hundreds we can help!</p>
  </div>

  <ul class="abs checklist" style="left:30px;top:469px">
    <li><svg viewBox="0 0 20 20"><circle cx="10" cy="10" r="10" fill="var(--pink)"/><path d="M5.5 10.5l3 3 6-6.5" fill="none" stroke="#fff" stroke-width="2"/></svg>Wedding Ceremonies</li>
    <li><svg viewBox="0 0 20 20"><circle cx="10" cy="10" r="10" fill="var(--pink)"/><path d="M5.5 10.5l3 3 6-6.5" fill="none" stroke="#fff" stroke-width="2"/></svg>Dancing on Clouds</li>
    <li><svg viewBox="0 0 20 20"><circle cx="10" cy="10" r="10" fill="var(--pink)"/><path d="M5.5 10.5l3 3 6-6.5" fill="none" stroke="#fff" stroke-width="2"/></svg>Lighting</li>
    <li><svg viewBox="0 0 20 20"><circle cx="10" cy="10" r="10" fill="var(--pink)"/><path d="M5.5 10.5l3 3 6-6.5" fill="none" stroke="#fff" stroke-width="2"/></svg>Monogram Lighting</li>
    <li><svg viewBox="0 0 20 20"><circle cx="10" cy="10" r="10" fill="var(--pink)"/><path d="M5.5 10.5l3 3 6-6.5" fill="none" stroke="#fff" stroke-width="2"/></svg>Photo Booth</li>
    <li><svg viewBox="0 0 20 20"><circle cx="10" cy="10" r="10" fill="var(--pink)"/><path d="M5.5 10.5l3 3 6-6.5" fill="none" stroke="#fff" stroke-width="2"/></svg>DJ Entertainment</li>
  </ul>

  <h3 class="abs section-title" style="left:452px;top:34px">Testimonial</h3>
  <p class="abs quote" style="left:452px;top:75px;width:192px">"I am so happy I hired A Spin Above Par for our wedding day! Dean was so fun and easy to work with — he listened to everything I wanted and delivered way above my expectations! Multiple people came up to us during and after the wedding to complement the DJ. Thank you so much Dean for helping to make our day so amazing. The dance floor was never empty and the energy was always high! You are the best!"</p>
  <div class="abs quote-author" style="left:452px;top:207px">Laura P.</div>

  <h3 class="abs section-title" style="left:376px;top:280px">Our Services</h3>
  <ul class="abs services" style="left:376px;top:316px;width:312px">
    <li>A highly trained and polished DJ and Master Of ceremonies (MC) who will coordinate with your venue and vendors to insure a smooth running event and a packed dance floor.</li>
    <li>Planning and coordination of your event</li>
    <li>Multiple Planning Sessions to help bring your vision to life</li>
    <li>Your own personal user name and password giving you access to our web based planning portal. It's easy, fun and takes away all of the stress of planning your event. You have <b>24×7</b> Access it via phone, tablet or computer. Now you can plan everything from your ceremony to reception music and traditional events at your convenience.</li>
    <li>We have state of the art equipment and visually attractive presentations</li>
    <li>A detailed Time line which will also be provided to all of the vendors working with us such as your venue or catering director, officiate, photographer, videographer and anyone else we will be working with who needs it.</li>
    <li><b>Ceremony Assistance:</b> (optional) We can also provide the music and sound system for your ceremony.</li>
  </ul>

  <h3 class="abs section-title" style="left:742px;top:428px">Corporate</h3>
  <div class="abs body-copy" style="left:742px;top:462px;width:288px">
    <p>With over 30+ years of experience providing DJ entertainment and lighting services for corporate events and company parties, we understand how important creating the right atmosphere and delivering quality entertainment is to the success of your event. So whether you're planning a sales incentive meeting, awards presentation, beach party, holiday party or gala evening, let us help you create an event your employees will never forget.</p>
    <p style="margin-top:4px">Our DJs are always ready to fill your dance floor so everyone can cut loose and enjoy a well-deserved break. If you would rather a more reserved approach, we can also provide a non-interactive style as well!</p>
  </div>
</section>
</div>

</body>
</html>
```